Professional Photography Business cards

I need business cards that include my logo which I have uploaded. I run a photography business. I am open to ideas but I would like one side to have my logo and the other side to have my contact info. I don't have a website made but I do own a website domain. I have uploaded 2 different logo color schemes. My business colors are Blue, black , and white.

Business Name
Business Phone Number
Business Email
Business Website address
Instagram

Industry/Entity Type

Professional Photography

Contact Information for Business Card

Phone Number: 916-384-7702 email: info@tlane-studio.example Instagram: @t.lanestudio website doman- www.tlane-studio.example

Requirements
Must have
• I like the idea of a business card with a full black background front and back of card. My colors must include royal blue, black, and white

```html
<!DOCTYPE html>
<html lang="en">
<head>
<meta charset="utf-8">
<title>T. Lane Studio — Business Cards</title>
<link href="https://fonts.googleapis.com/css2?family=Arimo:wght@400&display=swap" rel="stylesheet">
<style>
  :root {
    --backdrop: #2b2b2b;
    --card: #0b0b0b;
    --ink: #ffffff;
    --silver: #c4c4c4;
    --royal: #2f5fe0;
  }
  html, body {
    margin: 0;
    padding: 0;
    width: 1200px;
    height: 900px;
    overflow: hidden;
    background: var(--backdrop);
    font-family: "Arimo", Arial, sans-serif;
  }
  .sheet {
    width: 1200px;
    height: 900px;
    display: flex;
    align-items: center;
    justify-content: center;
    gap: 40px;
  }
  .card {
    width: 540px;
    height: 309px;
    background: var(--card);
    border-radius: 22px;
    position: relative;
    box-sizing: border-box;
  }
  .brand {
    display: flex;
    align-items: center;
    gap: 12px;
    color: var(--ink);
    font-weight: 400;
    white-space: nowrap;
  }
  .brand-dot {
    border: 2px solid var(--royal);
    border-radius: 50%;
    box-sizing: border-box;
    flex: none;
  }
  /* contact side */
  .card-contact .brand {
    position: absolute;
    left: 40px;
    top: 138px;
    font-size: 22px;
  }
  .card-contact .brand-dot { width: 22px; height: 22px; }
  .divider {
    position: absolute;
    left: 262px;
    top: 92px;
    width: 1px;
    height: 126px;
    background: var(--royal);
  }
  .contact-list {
    position: absolute;
    left: 284px;
    top: 100px;
    margin: 0;
    padding: 0;
    list-style: none;
    color: var(--ink);
    font-size: 13.5px;
    line-height: 1;
  }
  .contact-list li {
    display: flex;
    align-items: center;
    gap: 8px;
    margin-bottom: 9px;
  }
  .contact-list li.social { margin-top: 22px; }
  .contact-icon { width: 13px; height: 13px; flex: none; color: var(--royal); }
  .social-dot {
    width: 14px;
    height: 14px;
    border: 1.5px solid var(--royal);
    border-radius: 50%;
    box-sizing: border-box;
    flex: none;
  }
  /* logo side */
  .card-front .brand {
    position: absolute;
    left: 0;
    right: 0;
    top: 50%;
    transform: translateY(-50%);
    justify-content: center;
    color: var(--silver);
    font-size: 36px;
  }
  .card-front .brand-dot { width: 34px; height: 34px; }
</style>
</head>
<body>
<main class="sheet">
  <section class="card card-contact" aria-label="Contact side">
    <div class="brand"><span class="brand-dot"></span><span class="brand-name">T. Lane Studio</span></div>
    <div class="divider"></div>
    <ul class="contact-list">
      <li>
        <svg class="contact-icon" viewBox="0 0 24 24" fill="none" stroke="currentColor" stroke-width="2.2" stroke-linecap="round" stroke-linejoin="round"><path d="M22 16.9v3a2 2 0 0 1-2.2 2 19.8 19.8 0 0 1-8.6-3.1 19.5 19.5 0 0 1-6-6A19.8 19.8 0 0 1 2.1 4.2 2 2 0 0 1 4.1 2h3a2 2 0 0 1 2 1.7c.1 1 .4 1.9.7 2.8a2 2 0 0 1-.5 2.1L8 9.9a16 16 0 0 0 6 6l1.3-1.3a2 2 0 0 1 2.1-.4c.9.3 1.8.6 2.8.7a2 2 0 0 1 1.7 2z"/></svg>
        <span>916-384-7702</span>
      </li>
      <li>
        <svg class="contact-icon" viewBox="0 0 24 24" fill="currentColor"><path d="M2 5h20v14H2z"/><path d="M2 5l10 8 10-8" fill="none" stroke="#0b0b0b" stroke-width="1.8"/></svg>
        <span>info@tlane-studio.example</span>
      </li>
      <li>
        <svg class="contact-icon" viewBox="0 0 24 24" fill="none" stroke="currentColor" stroke-width="2"><circle cx="12" cy="12" r="10"/><path d="M2 12h20M12 2a15 15 0 0 1 0 20M12 2a15 15 0 0 0 0 20"/></svg>
        <span>www.tlane-studio.example</span>
      </li>
      <li class="social">
        <span class="social-dot"></span>
        <span>@t.lanestudio</span>
      </li>
    </ul>
  </section>

  <section class="card card-front" aria-label="Logo side">
    <div class="brand"><span class="brand-dot"></span><span class="brand-name">T. Lane Studio</span></div>
  </section>
</main>
</body>
</html>
```